Business Card Design for a Personal Trainer

I need a business card design for my job as a personal trainer. It should have a unique, modern and exclusive design. On the front there should be only my logo with my name and my job. 0162/3819204 Tobias Lendhart Wiesengrundweg 14 80417 Munich Germany The most important contact information is the web adress. it can be bigger than the rest, but its not necessary. The card should be 8,5cmx5,5cm big. Font: Roboto. Colors: black, white, gray, 56c1ff.

```html
<!DOCTYPE html>
<html lang="de">
<head>
<meta charset="utf-8">
<title>Tobias Lendhart – Personal Trainer Business Card</title>
<link href="https://fonts.googleapis.com/css2?family=Roboto:ital,wght@0,400;0,500;1,900&display=swap" rel="stylesheet">
<style>
  :root {
    --card-black: #0b0b0b;
    --white: #ffffff;
    --band-gray: #9d9d9d;
    --text-dark: #161616;
    --page-bg: #e9e7e4;
    --photo-light: #d8d8d8;
    --photo-dark: #3a3a3a;
  }
  * { margin: 0; padding: 0; box-sizing: border-box; }
  html, body { width: 1189px; height: 1200px; overflow: hidden; }
  body {
    background: var(--page-bg);
    font-family: "Roboto", sans-serif;
    position: relative;
  }
  .card {
    position: absolute;
    left: 202px;
    width: 784px;
    height: 506px;
    border-radius: 26px;
    overflow: hidden;
    background: var(--card-black);
    color: var(--white);
    box-shadow: 0 8px 24px rgba(0,0,0,0.25);
  }
  .card--front { top: 71px; }
  .card--back { top: 623px; }
  .card__art { position: absolute; inset: 0; width: 100%; height: 100%; }
  .brand { position: absolute; text-align: center; }
  .brand__square { display: block; margin: 0 auto; background: var(--white); }
  .brand__name { font-weight: 400; line-height: 1; white-space: nowrap; }
  .brand__role {
    display: flex; align-items: center; justify-content: center;
    font-weight: 400; letter-spacing: 0.3em; white-space: nowrap;
  }
  .brand__role::before, .brand__role::after {
    content: ""; height: 1.5px; background: var(--white); flex: 1;
  }
  .brand__role::before { margin-right: 6px; }
  .brand__role::after { margin-left: 2px; }
  .card--front .brand { left: 0; right: 0; top: 150px; }
  .card--front .brand__square { width: 58px; height: 58px; margin-bottom: 58px; }
  .card--front .brand__name { font-size: 41px; }
  .card--front .brand__role { font-size: 17px; width: 404px; margin: 8px auto 0; }
  .card--back .brand { left: 445px; width: 295px; top: 60px; }
  .card--back .brand__square { width: 48px; height: 48px; margin-bottom: 50px; }
  .card--back .brand__name { font-size: 33px; letter-spacing: -0.2px; }
  .card--back .brand__role { font-size: 14px; margin-top: 5px; }
  .website {
    position: absolute; bottom: 10px;
    font-weight: 900; font-style: italic;
    font-size: 21px; letter-spacing: 0.3em;
    color: var(--text-dark); white-space: nowrap;
  }
  .card--front .website { left: 0; right: 0; text-align: center; }
  .card--back .website { left: 313px; width: 420px; text-align: center; }
  .contact { position: absolute; left: 445px; width: 295px; text-align: center; }
  .contact__icon {
    display: block; width: 30px; height: 30px; margin: 0 auto 10px;
  }
  .contact__text { font-size: 22px; font-weight: 400; letter-spacing: 0.02em; }
  .contact--phone { top: 262px; padding-bottom: 12px; border-bottom: 1.5px solid var(--white); }
  .contact--mail { top: 349px; }
</style>
</head>
<body>

<section class="card card--front">
  <svg class="card__art" viewBox="0 0 784 506" preserveAspectRatio="none" aria-hidden="true">
    <rect x="0" y="449" width="784" height="7" fill="var(--white)"/>
    <rect x="0" y="456" width="784" height="50" fill="var(--band-gray)"/>
  </svg>
  <div class="brand">
    <span class="brand__square"></span>
    <p class="brand__name">TOBIAS LENDHART</p>
    <p class="brand__role">PERSONAL TRAINER</p>
  </div>
  <p class="website">www.YOURWEBSITE.com</p>
</section>

<section class="card card--back">
  <svg class="card__art" viewBox="0 0 922 595" preserveAspectRatio="none">
    <defs>
      <clipPath id="portrait-clip">
        <path d="M0 0 H430 C480 120 490 330 400 440 C340 510 280 530 240 535 H0 Z"/>
      </clipPath>
      <radialGradient id="portrait-tone" cx="0.45" cy="0.6" r="0.6">
        <stop offset="0" stop-color="var(--photo-dark)"/>
        <stop offset="0.7" stop-color="#6a6a6a"/>
        <stop offset="1" stop-color="var(--photo-light)"/>
      </radialGradient>
    </defs>
    <path d="M0 0 H430 C480 120 490 330 400 440 C340 510 280 530 240 535 H0 Z" fill="var(--white)"/>
    <path d="M430 0 H442 C505 130 510 345 422 452 C362 516 300 534 262 535 H240 C280 530 340 510 400 440 C490 330 480 120 430 0 Z" fill="var(--band-gray)"/>
    <g clip-path="url(#portrait-clip)" role="img" aria-label="Black and white portrait photo of the trainer, arms crossed">
      <rect x="0" y="20" width="400" height="520" fill="url(#portrait-tone)"/>
    </g>
    <rect x="0" y="530" width="922" height="9" fill="var(--white)"/>
    <rect x="0" y="539" width="922" height="56" fill="var(--band-gray)"/>
  </svg>

  <div class="brand">
    <span class="brand__square"></span>
    <p class="brand__name">TOBIAS LENDHART</p>
    <p class="brand__role">PERSONAL TRAINER</p>
  </div>

  <div class="contact contact--phone">
    <svg class="contact__icon" viewBox="0 0 30 30" aria-hidden="true">
      <circle cx="15" cy="15" r="15" fill="#8a8a8a"/>
      <path d="M8 12 Q15 6 22 12 L20 14 L18 12 L12 12 L10 14 Z" fill="var(--card-black)"/>
      <rect x="10" y="14" width="10" height="8" rx="1.5" fill="var(--card-black)"/>
      <circle cx="15" cy="18" r="2" fill="#8a8a8a"/>
    </svg>
    <p class="contact__text">0162/3819204</p>
  </div>

  <div class="contact contact--mail">
    <svg class="contact__icon" viewBox="0 0 30 30" aria-hidden="true">
      <circle cx="15" cy="15" r="15" fill="#8a8a8a"/>
      <rect x="8" y="10" width="14" height="10" fill="var(--card-black)"/>
      <path d="M8 10 L15 16 L22 10" fill="none" stroke="#8a8a8a" stroke-width="1.3"/>
    </svg>
    <p class="contact__text">info@lendhart-training.de</p>
  </div>

  <p class="website">www.YOURWEBSITE.com</p>
</section>

</body>
</html>
```